Web Design for a Biotech Consulting Firm

We need a web site design for a new business based in Philadelphia called Verantel Dx. This is a consulting firm that will serve medical diagnostics industry, which is part of the life science/healthcare industry focusing on developing and marketing products that help in early detection, monitoring or management of diseases. Our consulting firm will help medical diagnostic companies to overcome key challenges in designing, evaluating and marketing new products.Our company name is Verantel Dx. Verantel is Latin word for "something" Dx represents diagnostics. The idea behind the name is that we help companies to transform the original, early product ideas ("nothing") into "something"; which is a product with full clinical utility that will help to improve health and well-being.The web site should use the visual feel of the logo (attached), be modern, simple and clean looking and represent creativity, innovation, scientific thinking and progress.
Updates

Wix Design is acceptable

Industry/Entity Type

Biotechnology

Coding

Coded - Design and coding required

Number of Pages Required

1 page

Font styles to use
Sans Serif

Requirements
Must have
• simple, clean look couple of pages
Should not have
• a lot of pages

```html
<!DOCTYPE html>
<html lang="en">
<head>
<meta charset="utf-8">
<title>Verantel Dx — Medical Diagnostics Consulting</title>
<link href="https://fonts.googleapis.com/css2?family=Montserrat:ital,wght@0,400;0,500;0,600;0,700;1,500&display=swap" rel="stylesheet">
<style>
:root{
  --blue:#1a7cf0;
  --ink:#1d1d1f;
  --text:#4a4a50;
  --frame:#3a5f9a;
  --light:#f3f3f4;
  --white:#ffffff;
}
*{box-sizing:border-box;margin:0;padding:0}
html,body{width:1200px;height:5298px;overflow:hidden}
body{font-family:"Montserrat",Arial,sans-serif;color:var(--text);background:var(--white);position:relative}
section,header,footer{position:relative;width:1200px;overflow:hidden}

/* titles */
.section-title{position:absolute;display:inline-block;padding:18px;font-size:30px;font-weight:500;color:var(--ink);white-space:nowrap}
.section-title::before{content:"";position:absolute;left:0;top:0;width:66px;height:100%;border:3px solid var(--frame);border-right:none}
.section-title b{font-weight:700}
.section-title span{color:var(--blue)}
.on-dark{color:var(--white)}
.on-dark::before{border-color:var(--blue)}
.body-copy{font-size:16px;line-height:25px;color:var(--text)}
.btn{position:absolute;display:block;background:var(--blue);color:var(--white);font-size:12px;font-weight:700;letter-spacing:.5px;text-align:center;border-radius:4px;height:40px;line-height:40px;width:178px}

/* nav */
.nav{position:absolute;left:0;width:1200px;display:flex;justify-content:center;font-size:12px;color:#d8dde6;letter-spacing:.3px}
.nav a{padding:0 13px;height:52px;line-height:52px;color:inherit;text-decoration:none;text-transform:uppercase}
.nav a.current{color:var(--white);font-weight:700;border:2px solid var(--blue);border-right:none;border-bottom:none}

/* brand name: plain text, one colour, one weight */
.brand-name{position:absolute;left:0;width:1200px;text-align:center;font-weight:400;color:var(--white);white-space:nowrap;letter-spacing:1px}

/* hero */
.hero{height:570px;background:linear-gradient(135deg,#5b6472 0%,#8c96a4 35%,#6b7584 60%,#2f3540 100%)}
.hero-photo{position:absolute;inset:0;background:radial-gradient(ellipse at 55% 40%,rgba(210,220,232,.55),rgba(60,68,80,.2) 60%,rgba(20,24,30,.5))}

/* intro band */
.intro{height:200px;background:linear-gradient(90deg,#121316,#2a2b2e 60%,#1c1c1e)}
.intro-blue{position:absolute;left:0;top:0;width:600px;height:200px;background:var(--blue);clip-path:polygon(0 0,100% 0,92% 100%,0 100%)}
.intro-head{position:absolute;left:48px;top:62px;font-size:29px;line-height:36px;color:var(--white);font-weight:400}
.intro-head b{font-weight:700}
.intro-text{position:absolute;left:604px;top:52px;width:560px;font-size:15.5px;line-height:24px;color:#e6e6e6}

/* about */
.about{height:475px}
.about .body-copy{position:absolute;left:100px;width:1000px;text-align:center}

/* feature rows */
.feature{height:455px}
.feature.gray{background:var(--light)}
.feature.dark{background:linear-gradient(100deg,#040507,#121722 50%,#06070a);height:460px}
.feature .body-copy{position:absolute;width:490px}
.feature.dark .body-copy{color:#cfd2d8}
.photo{position:absolute;box-shadow:0 10px 18px rgba(0,0,0,.25)}

/* news */
.news{height:700px;background:var(--light)}
.news-card{position:absolute;top:199px;width:331px}
.news-img{width:331px;height:204px}
.news-date{margin-top:30px;font-size:14px;color:var(--text);display:flex;align-items:center;gap:10px}
.news-head{margin-top:16px;font-size:15px;color:var(--ink);font-weight:500;line-height:22px}
.news-text{font-size:14px;line-height:22px;color:var(--text)}
.news-more{margin-top:26px;font-size:13px;color:var(--blue)}

/* testimonials */
.testimonials{height:731px;background:linear-gradient(180deg,#1b1f27,#2b313c 45%,#0f1217)}
.quote{position:absolute;padding:22px 24px;font-size:13.5px;line-height:24px;color:#eef0f3}
.quote.one{left:93px;top:201px;width:516px;height:164px;background:rgba(35,40,50,.85)}
.quote.two{left:591px;top:259px;width:516px;height:172px;background:rgba(130,136,148,.6)}
.avatar{position:absolute;width:96px;height:96px;border-radius:50%;border:4px solid var(--white);background:linear-gradient(180deg,#cfd4dc,#8d96a4)}
.person{position:absolute;font-size:17px;font-style:italic;font-weight:500;color:var(--white)}
.dots{position:absolute;left:562px;top:626px;display:flex;gap:5px}
.dots i{width:13px;height:13px;border-radius:50%;border:2px solid var(--white)}
.dots i.on{background:var(--white)}

/* clients */
.clients{height:349px}
.client-row{position:absolute;top:225px;left:0;width:1200px;display:flex;justify-content:center;gap:62px;font-size:30px;font-weight:700;color:#8e9197;letter-spacing:1px}

/* contact */
.contact{height:517px;background:var(--light)}
.field{position:absolute;background:var(--white);font-size:12px;color:var(--ink);padding:16px 18px}
.contact-info{position:absolute;left:882px;font-size:15px;line-height:26px;color:var(--ink)}
.contact-line{display:flex;gap:10px;align-items:flex-start}

/* footer */
.footer{height:344px;background:linear-gradient(180deg,#1e2026,#2b2d33 60%,#141519)}
.copyright{position:relative;height:40px;background:var(--white);font-size:9px;color:var(--ink);padding-left:28px;line-height:40px}
.socials{position:absolute;right:26px;top:10px;display:flex;gap:4px}
.socials i{width:20px;height:20px;border-radius:50%;border:1.5px solid var(--ink)}
</style>
</head>
<body>

<header class="hero">
  <div class="hero-photo" role="img" aria-label="Laboratory scientist holding a tablet, soft blue-grey tone"></div>
  <div class="brand-name" style="top:250px;font-size:52px">Verantel Dx</div>
  <nav class="nav" style="top:472px">
    <a class="current">Home</a><a>About</a><a>Services</a><a>Clients</a><a>Testimonials</a><a>News</a><a>Contact</a>
  </nav>
</header>

<section class="intro">
  <div class="intro-blue"></div>
  <h1 class="intro-head"><b>DESIGNING, EVALUATING,</b><br>MARKETING NEW PRODUCTS</h1>
  <p class="intro-text">We are a consulting firm that will serve medical diagnostics industry, which is part of the life science/healthcare industry focusing on developing and marketing products that help in early detection, monitoring or management of diseases.</p>
</section>

<section class="about">
  <h2 class="section-title" style="left:464px;top:110px"><b>ABOUT</b> Verantel <span>DX</span></h2>
  <p class="body-copy" style="top:248px">Lorem ipsum dolor sit amet, consectetuer adipiscing elit, sed diam nonummy nibh euismod tincidunt ut laoreet dolore magna aliquam erat volutpat. Ut wisi enim ad minim veniam, quis nostrud exerci tation ullamcorper suscipit lobortis nisl ut aliquip ex ea commodo consequat. Duis autem veleum iriure dolor in hendrerit in vul putate velit esse molestie consequat, vel illum dolore eu feugiat nulla facilisis at vero eros et accumsan.</p>
  <a class="btn" style="left:511px;top:358px">LEARN MORE</a>
</section>

<section class="feature gray">
  <h2 class="section-title" style="left:72px;top:90px"><b>NEW</b> Product <span>Design</span></h2>
  <p class="body-copy" style="left:76px;top:200px">Lorem ipsum dolor sit amet, consectetuer adipiscing elit, sed diam nonummy nibh euismod tincidunt ut laoreet dolore magna aliquam erat volutpat. Ut wisi enim ad veniam quis nostrud exerci tation.</p>
  <a class="btn" style="left:74px;top:330px">LEARN MORE</a>
  <div class="photo" style="left:628px;top:93px;width:498px;height:270px;background:linear-gradient(135deg,#e9f0f7,#8fb3d9 50%,#d7e3ef)" role="img" aria-label="Doctor using a transparent digital display"></div>
</section>

<section class="feature dark">
  <div class="photo" style="left:74px;top:93px;width:498px;height:271px;background:linear-gradient(135deg,#dfe6ee,#aebdd0 45%,#e8ecf1)" role="img" aria-label="Hand touching a tablet showing bar charts"></div>
  <h2 class="section-title on-dark" style="left:628px;top:88px"><b>PRODUCT</b> <span>Evaluation</span></h2>
  <p class="body-copy" style="left:630px;top:193px">Lorem ipsum dolor sit amet, consectetuer adipiscing elit, sed diam nonummy nibh euismod tincidunt ut laoreet dolore magna aliquam erat volutpat. Ut wisi enim ad veniam quis nostrud exerci tation.</p>
  <a class="btn" style="left:628px;top:318px">LEARN MORE</a>
</section>

<section class="feature">
  <h2 class="section-title" style="left:72px;top:88px"><b>NEW</b> Product <span>Marketing</span></h2>
  <p class="body-copy" style="left:76px;top:198px">Lorem ipsum dolor sit amet, consectetuer adipiscing elit, sed diam nonummy nibh euismod tincidunt ut laoreet dolore magna aliquam erat volutpat. Ut wisi enim ad veniam quis nostrud exerci tation.</p>
  <a class="btn" style="left:74px;top:328px">LEARN MORE</a>
  <div class="photo" style="left:628px;top:92px;width:498px;height:271px;background:linear-gradient(180deg,#b8cde0,#d9c9a6 60%,#6b5a44)" role="img" aria-label="Businessman with a megaphone on a hilltop"></div>
</section>

<section class="news">
  <h2 class="section-title" style="left:496px;top:85px"><b>LATEST</b> <span>News</span></h2>
  <article class="news-card" style="left:74px">
    <div class="news-img" style="background:linear-gradient(135deg,#cfdbe8,#6f8fb4)" role="img" aria-label="Laboratory microscope"></div>
    <div class="news-date"><svg width="16" height="16" viewBox="0 0 16 16"><rect x="1" y="3" width="14" height="12" fill="none" stroke="#1a7cf0" stroke-width="1.5"/><path d="M1 6h14M5 1v4M11 1v4" stroke="#1a7cf0" stroke-width="1.5"/></svg>Jan 14, 2019</div>
    <p class="news-head">Duis aute irure dolor in reprehen</p>
    <p class="news-text">Lorem ipsum dolor sit amet, cons ectetur adipiscing elit, sed do eius mod tempor incididunt.</p>
    <p class="news-more">Read more...</p>
  </article>
  <article class="news-card" style="left:434px">
    <div class="news-img" style="background:linear-gradient(135deg,#e3ebf3,#7fa6cf)" role="img" aria-label="Scientist working at a microscope"></div>
    <div class="news-date"><svg width="16" height="16" viewBox="0 0 16 16"><rect x="1" y="3" width="14" height="12" fill="none" stroke="#1a7cf0" stroke-width="1.5"/><path d="M1 6h14M5 1v4M11 1v4" stroke="#1a7cf0" stroke-width="1.5"/></svg>Jan 14, 2019</div>
    <p class="news-head">Duis aute irure dolor in reprehen</p>
    <p class="news-text">Lorem ipsum dolor sit amet, cons ectetur adipiscing elit, sed do eius mod tempor incididunt.</p>
    <p class="news-more">Read more...</p>
  </article>
  <article class="news-card" style="left:795px">
    <div class="news-img" style="background:linear-gradient(135deg,#27303d,#7a8698 55%,#1b2029)" role="img" aria-label="Hands fitting puzzle pieces together"></div>
    <div class="news-date"><svg width="16" height="16" viewBox="0 0 16 16"><rect x="1" y="3" width="14" height="12" fill="none" stroke="#1a7cf0" stroke-width="1.5"/><path d="M1 6h14M5 1v4M11 1v4" stroke="#1a7cf0" stroke-width="1.5"/></svg>Jan 14, 2019</div>
    <p class="news-head">Duis aute irure dolor in reprehen</p>
    <p class="news-text">Lorem ipsum dolor sit amet, cons ectetur adipiscing elit, sed do eius mod tempor incididunt.</p>
    <p class="news-more">Read more...</p>
  </article>
</section>

<section class="testimonials" role="img" aria-label="Night city street with light trails, dark blue tone">
  <h2 class="section-title on-dark" style="left:419px;top:87px"><b>CUSTOMER</b> <span>Testimonials</span></h2>
  <blockquote class="quote one">Lorem ipsum dolor sit amet, consectetur adipiscing elit, sed do eiusmod tempor incididunt ut labore et dolore magna aliqua. Ut enim ad minim veniam, quis nostrud exercitation ullamco laboris nisi ut aliquip ex. Duis aute irure dolor in reprehenderit in voluptate velit esse.</blockquote>
  <div class="avatar" style="left:103px;top:408px"></div>
  <p class="person" style="left:220px;top:444px">Marla Jennet</p>
  <blockquote class="quote two">Lorem ipsum dolor sit amet, consectetur adipiscing elit, sed do eiusmod tempor incididunt ut labore et dolore magna aliqua. Ut enim ad minim veniam, quis nostrud exercitation ullamco laboris nisi ut aliquip ex. Duis aute irure dolor in reprehenderit in voluptate velit esse.</blockquote>
  <div class="avatar" style="left:607px;top:464px"></div>
  <p class="person" style="left:710px;top:500px">Helen Obrey</p>
  <div class="dots"><i class="on"></i><i></i><i></i><i></i></div>
</section>

<section class="clients">
  <h2 class="section-title" style="left:503px;top:90px"><b>OUR</b> <span>Clients</span></h2>
  <div class="client-row"><span>Norvexa</span><span>Quillon</span><span>Pellarin</span><span>Tessary</span><span>Brindmark</span></div>
</section>

<section class="contact">
  <h2 class="section-title" style="left:72px;top:90px"><b>Send</b> <span>a Message</span></h2>
  <div class="field" style="left:74px;top:181px;width:240px;height:48px">Your Name</div>
  <div class="field" style="left:327px;top:181px;width:240px;height:48px">Your Email</div>
  <div class="field" style="left:580px;top:181px;width:241px;height:48px">Your Subject</div>
  <div class="field" style="left:74px;top:239px;width:747px;height:133px">Message</div>
  <a class="btn" style="left:358px;top:388px;height:38px;line-height:38px">SUBMIT</a>

  <h2 class="section-title" style="left:880px;top:90px"><b>Contact</b> <span>Us</span></h2>
  <div class="contact-info" style="top:172px">
    <div class="contact-line"><svg width="16" height="18" viewBox="0 0 16 18" style="margin-top:4px"><path d="M8 17s6-6 6-10A6 6 0 0 0 2 7c0 4 6 10 6 10z" fill="none" stroke="#1d1d1f" stroke-width="1.4"/><circle cx="8" cy="7" r="2" fill="#1d1d1f"/></svg><div>VERANTEL DX<br>418 Walnut Row<br>SUITE 210<br>Philadelphia, PA 19106</div></div>
    <div class="contact-line" style="margin-top:22px"><svg width="16" height="16" viewBox="0 0 16 16" style="margin-top:5px"><circle cx="8" cy="8" r="7" fill="none" stroke="#1d1d1f" stroke-width="1.3"/><path d="M5 4.5l1.5 0 .7 2-1 .8a5 5 0 0 0 2.5 2.5l.8-1 2 .7v1.5c-3.5.4-7-3-6.5-6.5z" fill="#1d1d1f"/></svg>(215) 555-0148</div>
    <div class="contact-line" style="margin-top:26px"><svg width="16" height="16" viewBox="0 0 16 16" style="margin-top:5px"><circle cx="8" cy="8" r="7" fill="none" stroke="#1d1d1f" stroke-width="1.3"/><rect x="4.5" y="5.5" width="7" height="5" fill="none" stroke="#1d1d1f"/><path d="M4.5 5.5 8 8.5l3.5-3" fill="none" stroke="#1d1d1f"/></svg>info@veranteldx.com</div>
  </div>
</section>

<footer class="footer">
  <div class="brand-name" style="top:132px;font-size:28px;color:#e8eaee">Verantel Dx</div>
  <nav class="nav" style="top:262px">
    <a class="current">Home</a><a>About</a><a>Services</a><a>Clients</a><a>Testimonials</a><a>News</a><a>Contact</a>
  </nav>
</footer>
<div class="copyright">COPYRIGHT © 2019 VERANTEL DX. ALL RIGHTS RESERVED.
  <div class="socials"><i></i><i></i><i></i></div>
</div>

</body>
</html>
```